Natural healthcare clinic needs stationery and business card design

We have had a logo developed by Pixel Harbor and are now looking at utilising it for a new business concept. The concept is a natural healthcare clinic that hosts a number of small businesses. The individual practitioners may want to utilise the host business stationery to provide a consistent message to clients.

I am looking for a stationery design - letterhead, DL brochure template and business card that uses our logo. The business name 'Bright Meadows' is all about getting rhythm back into your life so you can be fit and healthy. The stationery design should reflect this.

There are a couple of requirements for the business card, it needs to be double-sided with black and white back. There should be lines to write appointment times on. The cards may need to be custom named on the front for example Carol Fenwick, Remedial Therapist and Aromatherapist. Therefore if a template can be provided so we can customise this information using MS Publisher, it would be appreciated.

The DL brochure template needs to be A4 folded to DL. I am looking for a consistent brand message that can be utilised to produce our own clinic brochures.

The natural healthcare clinic will host the following types of businesses - remedial massage, pregnancy massage, oncology massage, aromatherapy, acupuncture - as a bit of a guide.

Target Market(s)

25-45 year old male and females who work full time.

Industry/Entity Type

Healthcare

Requirements
Must have
• Use the logo I have already.

```html
<!DOCTYPE html>
<html lang="en">
<head>
<meta charset="utf-8">
<title>Bright Meadows Letterhead</title>
<link rel="stylesheet" href="https://fonts.googleapis.com/css2?family=Open+Sans:wght@400;600&display=swap">
<style>
  :root {
    --backdrop: #ece8e2;
    --paper: #ffffff;
    --leaf-green: #84b12c;
    --leaf-green-light: #a6cb3d;
    --olive: #5f6f1d;
    --peach: #f6bf98;
    --peach-faint: #fbeee4;
    --text-dark: #4a4a4a;
    --brand-green: #7c9a2a;
    --icon-orange: #e98a2f;
  }
  * { margin: 0; padding: 0; box-sizing: border-box; }
  html, body {
    width: 1200px;
    height: 1024px;
    overflow: hidden;
    background: var(--backdrop);
    font-family: "Open Sans", sans-serif;
  }
  .letterhead {
    position: absolute;
    left: 260px;
    top: 32px;
    width: 680px;
    height: 960px;
    background: var(--paper);
    box-shadow: 0 6px 24px rgba(0,0,0,0.18);
    overflow: hidden;
  }
  .brand {
    position: absolute;
    left: 44px;
    top: 62px;
    display: flex;
    align-items: center;
    gap: 10px;
  }
  .brand-dot {
    width: 22px;
    height: 22px;
    border-radius: 50%;
    background: var(--leaf-green);
  }
  .brand-name {
    font-size: 26px;
    font-weight: 600;
    color: var(--brand-green);
    letter-spacing: -0.3px;
  }
  .contact {
    position: absolute;
    right: 44px;
    top: 70px;
    font-size: 10.5px;
    line-height: 1.45;
    color: var(--text-dark);
    width: 170px;
  }
  .contact-row {
    display: flex;
    align-items: center;
    gap: 5px;
  }
  .contact-row svg { flex: none; }
  .watermark {
    position: absolute;
    left: 70px;
    top: 240px;
    width: 480px;
    height: 420px;
  }
  .footer-band {
    position: absolute;
    left: 0;
    bottom: 0;
    width: 680px;
    height: 220px;
  }
  .website {
    position: absolute;
    left: 40px;
    bottom: 62px;
    font-size: 11px;
    color: #ffffff;
    letter-spacing: 0.3px;
  }
</style>
</head>
<body>
  <main class="letterhead">
    <header class="brand">
      <span class="brand-dot"></span>
      <span class="brand-name">Bright Meadows</span>
    </header>

    <address class="contact" style="font-style: normal;">
      <div>Your address Goes Here, City,<br>Zip Code, Country Name</div>
      <div class="contact-row">
        <svg width="9" height="9" viewBox="0 0 10 10"><path d="M2 1 L4 1 L4.6 3 L3.5 4 Q4.5 6 6 6.5 L7 5.4 L9 6 L9 8 Q5 9.5 2 6 Q0.5 3 2 1 Z" fill="var(--icon-orange)"/></svg>
        <span>322-4565-8977</span>
      </div>
      <div class="contact-row">
        <svg width="9" height="9" viewBox="0 0 10 10"><rect x="1" y="3" width="8" height="6" rx="1" fill="var(--icon-orange)"/><rect x="3" y="1" width="4" height="3" fill="var(--icon-orange)"/></svg>
        <span>322-7859-8559</span>
      </div>
      <div class="contact-row">
        <svg width="9" height="9" viewBox="0 0 10 10"><rect x="0.5" y="2" width="9" height="6.5" rx="1" fill="var(--icon-orange)"/><path d="M1 2.5 L5 5.5 L9 2.5" stroke="#fff" stroke-width="0.9" fill="none"/></svg>
        <span>name@domainname.com</span>
      </div>
    </address>

    <svg class="watermark" role="img" aria-label="Faint background watermark area for the clinic emblem" viewBox="0 0 480 420">
      <defs>
        <radialGradient id="watermarkGlow" cx="50%" cy="55%" r="55%">
          <stop offset="0%" stop-color="var(--peach-faint)" stop-opacity="0.9"/>
          <stop offset="100%" stop-color="var(--peach-faint)" stop-opacity="0"/>
        </radialGradient>
      </defs>
      <ellipse cx="240" cy="220" rx="240" ry="200" fill="url(#watermarkGlow)"/>
    </svg>

    <svg class="footer-band" viewBox="0 0 680 220" preserveAspectRatio="none" aria-hidden="true">
      <defs>
        <linearGradient id="bandGreen" x1="0" y1="0" x2="1" y2="1">
          <stop offset="0%" stop-color="var(--leaf-green)"/>
          <stop offset="60%" stop-color="var(--leaf-green-light)"/>
          <stop offset="100%" stop-color="var(--leaf-green)"/>
        </linearGradient>
      </defs>
      <path d="M0 18 Q120 0 260 60 Q420 130 680 150 L680 220 L0 220 Z" fill="var(--peach)"/>
      <path d="M0 28 Q120 12 260 70 Q420 140 680 158 L680 220 L0 220 Z" fill="#ffffff"/>
      <path d="M0 36 Q120 22 260 80 Q420 150 680 168 L680 220 L0 220 Z" fill="url(#bandGreen)"/>
      <path d="M200 40 Q320 70 430 122 Q540 160 680 150 L680 156 Q540 170 428 130 Q320 80 200 40 Z" fill="var(--olive)"/>
    </svg>

    <div class="website">www.websitename.com</div>
  </main>
</body>
</html>
```